Online Psychiatry business - Business Card

I need a business card design. The target audience is busy professionals of any field (this therapy appeals best to 24-35 year olds). It involves psychiatry by tele-medicine (or video-conference). Nothing on it should be a giveaway that it's about mental health. Professional design with silver or gold as the primary colors appeals to me. The card must be as simple and as uncluttered as possible. Some color and flowing design on the edge of the card appeals to me.
CalmHarborDirect.net should probably appear in the center of the card and stand out, i.e. bold lettering, and easy to read, no cursive, but Ariel Black. Some where below this, should appear "Too Busy to Take Care of Yourself? Think again." Since this isn't office based, I don't think an office address is necessary and limits clutter.
Information that does need to appear is my name: Gerald Mossvane, MD
General phone number: 555-417-8062. I'm hoping to get an 24-hour answering service soon so leave a little room for this. In addition I want to include two email addresses:
CalmHarborDirect@mailbox-example.net and CalmHarbor247@mailbox-example.net
Updates

I like the designs. I would like someone to put the website in bold in the center

 as most have been doing with a smaller font reminder nearby saying "No time" etc.
but I'd like to put my name down in the corner with the rest of the contact material.
Black print against a white or grey background appeals to me, with darker silver artwork near the sides (simple abstract, like wavy lines or something you can one up with that works. 
thanks

I ve tried to provide as much feedback as possible given my time limits, so if you have extra questions, please feel free to email. I tried to attach a file of a business card I really like but make be difficult to actually manufacture. I'm going to send you a link to the photo. The card has a pull tab. There is not much information on the outside. In fact, if you were to design the outside, I would just print : Too Busy to Take Care of Yourself? Think Again.

When you pull the tab the remaining information is on the bottom half of the card. Please don't use the color pink!!!!
http://www.cardgallery-example.org/2009/05/100-clever-print-ideas/
It is the 39th photo on the list, about 2/3ds of the way down the page. It is titled: Faltenkiste

#7 and #16 have an appeal to me, except for the dot patterns
Hope this helps

I'm running out of time and energy. I 've been trying to give do down the list and give  individual feedback but I won't be able to do that anymore.

So if you have any specific questions, write me, and again thank you for all your effort!!

I know i received your files, including your zip files, Pindrel,

but Milo, did you send me the files including ZIP on project 6143907?
thanks

Target Market(s)

Working professionals and executive, attorneys, etc.

Industry/Entity Type

Business

Logo Text

Don't Have Time to Take Care of Yourself? Think Again.

Logo styles of interest
Pictorial/Combination Logo
Wordmark Logo
Font styles to use
Other font styles liked:
• Ariel Black appeals to me the most

Requirements
Must have
• Want to emphasize that the website must be obvious, easily found (The CalmHarborDirect.net)
For that reason i'd like the card to be white, and minimal decoration on one or both sides just to add some style and color
Nice to have
• A Very uncluttered, elegant design, and something that makes it stick in your head-doesn't everyone want the last?
Should not have
• Nothing on the card that give it away that this is about psychiatry, such as brain or other symbol, but also nothing that gives it away as a medical business, such as a stethoscope or red cross or anything.

```html
<!DOCTYPE html>
<html lang="en">
<head>
<meta charset="utf-8">
<title>CalmHarborDirect.net — Business Card</title>
<link rel="stylesheet" href="https://fonts.googleapis.com/css2?family=Arimo:wght@400;700&display=swap">
<style>
  :root {
    --backdrop: #5a4a3e;
    --card-white: #ffffff;
    --card-grey: #ececec;
    --gold-light: #f6ea98;
    --gold-mid: #ead063;
    --gold-deep: #d6ad2c;
    --ink-dark: #333333;
    --ink-black: #111111;
    --ink-soft: #4a3c10;
    --swoosh-dark: #3a3a3a;
    --swoosh-light: #9a9a9a;
    --tagline-gold: #d9a418;
    --text-white: #ffffff;
  }
  * { box-sizing: border-box; margin: 0; padding: 0; }
  html, body {
    width: 1200px;
    height: 418px;
    overflow: hidden;
    background: var(--backdrop);
    font-family: "Arimo", Arial, sans-serif;
  }
  .card {
    position: absolute;
    top: 91px;
    width: 464px;
    height: 264px;
    overflow: hidden;
  }
  .card--front {
    left: 124px;
    background: radial-gradient(ellipse at 50% 50%, var(--card-white) 55%, var(--card-grey) 100%);
  }
  .card--back {
    left: 628px;
    background: linear-gradient(180deg, var(--gold-light) 0%, var(--gold-mid) 55%, var(--gold-deep) 100%);
    text-align: center;
  }
  .card__edges {
    position: absolute;
    inset: 0;
  }
  .front__site {
    position: absolute;
    top: 60px;
    left: 0;
    width: 100%;
    text-align: center;
    font-weight: 700;
    font-size: 29px;
    line-height: 34px;
    color: var(--ink-dark);
  }
  .front__tagline {
    position: absolute;
    top: 105px;
    left: 0;
    width: 100%;
    text-align: center;
    font-size: 12.5px;
    color: var(--tagline-gold);
  }
  .front__contact {
    position: absolute;
    top: 160px;
    left: 0;
    width: 100%;
    text-align: center;
    font-size: 11px;
    color: var(--ink-black);
    line-height: 17px;
  }
  .front__name { font-weight: 700; font-size: 12px; margin-bottom: 2px; }
  .front__phone { margin-bottom: 5px; }
  .front__phone strong { font-size: 13px; font-weight: 700; margin-left: 3px; }
  .back__site {
    position: absolute;
    top: 92px;
    left: 0;
    width: 100%;
    font-weight: 700;
    font-size: 29px;
    line-height: 34px;
    color: var(--text-white);
    text-shadow: 1px 2px 3px rgba(0,0,0,0.45);
  }
  .back__tagline {
    position: absolute;
    top: 137px;
    left: 0;
    width: 100%;
    font-weight: 700;
    font-size: 11px;
    color: var(--ink-black);
    letter-spacing: 0.3px;
  }
  .back__reminder {
    position: absolute;
    top: 170px;
    left: 0;
    width: 100%;
    font-size: 11.5px;
    color: var(--ink-soft);
  }
  .back__service {
    position: absolute;
    top: 224px;
    left: 0;
    width: 100%;
    font-weight: 700;
    font-size: 11.5px;
    color: var(--text-white);
    letter-spacing: 0.2px;
  }
</style>
</head>
<body>
  <section class="card card--front">
    <svg class="card__edges" viewBox="0 0 464 264" width="464" height="264" aria-hidden="true">
      <defs>
        <linearGradient id="edgeGold" x1="0" y1="0" x2="1" y2="1">
          <stop offset="0" stop-color="#f7e27a"/>
          <stop offset="1" stop-color="#d9b030"/>
        </linearGradient>
      </defs>
      <path d="M0,0 H100 Q24,12 0,90 Z" fill="url(#edgeGold)"/>
      <path d="M100,0 Q24,12 0,90" fill="none" stroke="var(--swoosh-light)" stroke-width="3"/>
      <path d="M90,3 Q28,20 4,80" fill="none" stroke="var(--swoosh-dark)" stroke-width="4"/>
      <path d="M464,170 Q440,248 350,264 H464 Z" fill="url(#edgeGold)"/>
      <path d="M464,170 Q440,248 350,264" fill="none" stroke="var(--swoosh-light)" stroke-width="3"/>
      <path d="M460,180 Q432,250 360,261" fill="none" stroke="var(--swoosh-dark)" stroke-width="4"/>
    </svg>
    <h1 class="front__site">CalmHarborDirect.net</h1>
    <p class="front__tagline">"You're a amazing person. We should talk again."</p>
    <div class="front__contact">
      <p class="front__name">Gerald Mossvane, MD</p>
      <p class="front__phone">General Phone: <strong>555-417-8062</strong></p>
      <p class="front__email">CalmHarborDirect@mailbox-example.net</p>
      <p class="front__email">CalmHarbor247@mailbox-example.net</p>
    </div>
  </section>

  <section class="card card--back">
    <h2 class="back__site">CalmHarborDirect.net</h2>
    <p class="back__tagline">“NOT ENOUGH TIME TO CARE FOR YOURSELF”</p>
    <p class="back__reminder">Too Busy to Take Care of Yourself? Think again.</p>
    <p class="back__service">24-HOUR ANSWERING SERVICE</p>
  </section>
</body>
</html>
```